Professional & attention grabbing.

A business card design, front and back. I already have a logo I will attach, but I am open to something new as well.
Things to include:
Name:
Title:
Phone:
Email:
Wanting something that is professional but attention grabbing.
Also we do a lot of work using drones on natural gas pipelines (leading the future)if you want to include any of that. I'm open to ideas.
Target Market(s)
Natural gas transmission industry / greenhouse gas mitigation industry
Industry/Entity Type
Business
Colors
Designer to choose colors to be used in the design.
Look and feel
Each slider illustrates characteristics of the customer's brand and the style your logo design should communicate.

```html
<!DOCTYPE html>
<html lang="en">
<head>
<meta charset="utf-8">
<title>Kestrel Field Inspections – Business Card</title>
<link rel="stylesheet" href="https://fonts.googleapis.com/css2?family=Saira:wght@400;500;600;700&display=swap">
<style>
  :root {
    --backdrop: #878787;
    --card: #ffffff;
    --panel: #f3f3f3;
    --brand-red: #c01f25;
    --ink: #3a3a3c;
    --ink-soft: #444446;
  }
  * { margin: 0; padding: 0; box-sizing: border-box; }
  html, body { width: 1200px; height: 900px; overflow: hidden; }
  body {
    background: var(--backdrop);
    font-family: "Saira", sans-serif;
    position: relative;
  }
  .card {
    position: absolute;
    top: 271px;
    width: 458px;
    height: 282px;
    border-radius: 10px;
    overflow: hidden;
    background: var(--card);
  }
  .card--front { left: 137px; }
  .card--back { left: 626px; }

  .front__panel {
    position: absolute;
    left: 392px; top: 0; right: 0; height: 212px;
    background: linear-gradient(180deg, #f6f6f6, var(--panel));
  }
  .brand {
    position: absolute;
    display: flex;
    align-items: center;
    gap: 10px;
  }
  .brand__mark { width: 30px; height: 30px; }
  .brand__name {
    font-weight: 700;
    font-size: 25px;
    line-height: 1;
    letter-spacing: 0.5px;
  }
  .front .brand { left: 28px; top: 28px; }
  .card--front .brand__mark { background: var(--brand-red); }
  .card--front .brand__name { color: var(--ink); }

  .person { position: absolute; left: 28px; top: 161px; }
  .person__name {
    color: var(--brand-red);
    font-weight: 600;
    font-size: 19px;
    line-height: 22px;
    letter-spacing: 0.3px;
  }
  .person__title {
    color: var(--ink);
    font-weight: 500;
    font-size: 13px;
    line-height: 16px;
    letter-spacing: 0.5px;
  }
  .contacts { position: absolute; left: 28px; top: 218px; list-style: none; }
  .contacts li {
    display: flex; align-items: center; gap: 8px;
    color: var(--ink-soft); font-size: 13px; line-height: 21px;
  }
  .contacts svg { width: 11px; height: 11px; flex: none; }
  .address {
    position: absolute; right: 29px; top: 222px;
    text-align: right; color: var(--ink-soft);
    font-size: 13px; line-height: 17px; font-style: normal;
  }
  .front__bar {
    position: absolute; bottom: 0; height: 13px;
  }
  .front__bar--red { left: 0; width: 225px; background: var(--brand-red); }
  .front__bar--dark { left: 232px; right: 0; background: var(--ink); }

  .back__field {
    position: absolute; left: 0; right: 0; top: 12px; bottom: 13px;
    background: var(--brand-red);
  }
  .card--back .brand {
    left: 50%; top: 50%; transform: translate(-50%, -50%);
  }
  .card--back .brand__mark { background: #ffffff; }
  .card--back .brand__name { color: #ffffff; }
</style>
</head>
<body>
  <section class="card card--front front" aria-label="Business card front">
    <div class="front__panel"></div>
    <div class="brand">
      <span class="brand__mark"></span>
      <span class="brand__name">KESTREL FIELD</span>
    </div>
    <div class="person">
      <p class="person__name">DANA MARLOW</p>
      <p class="person__title">DIRECTOR</p>
    </div>
    <ul class="contacts">
      <li>
        <svg viewBox="0 0 11 11" aria-hidden="true"><rect width="11" height="11" fill="#c01f25"/><path d="M3 3.2h5v1.2l-1 .6v1.5H4V5L3 4.4z" fill="#fff"/></svg>
        555-014-2290
      </li>
      <li>
        <svg viewBox="0 0 11 11" aria-hidden="true"><rect width="11" height="11" fill="#c01f25"/><rect x="2.5" y="3.5" width="6" height="4" fill="#fff"/><path d="M2.5 3.5l3 2.2 3-2.2" stroke="#c01f25" stroke-width=".7" fill="none"/></svg>
        hello@kestrelfield.com
      </li>
    </ul>
    <address class="address">418 Harlow Street,<br>Ridgefield Park, Ostend</address>
    <div class="front__bar front__bar--red"></div>
    <div class="front__bar front__bar--dark"></div>
  </section>

  <section class="card card--back" aria-label="Business card back">
    <div class="back__field"></div>
    <div class="brand">
      <span class="brand__mark"></span>
      <span class="brand__name">KESTREL FIELD</span>
    </div>
  </section>
</body>
</html>
```